verdant terraces simple classy business card design

my name is colin barrow and I run a gardening business aimed at high class verdant terraces. the business name is verdant terraces and our logo was designed on pixel harbour .My clientel are anything from residential homes to businesses. I take pride in my work and know that I offer a service like no other in my area.
The business card will be used to represent my business and I want it to be not only rememberable, but simplistic and modern. Eye catching too. Of course I would like it relatable to gardening and appealing to the correct clientel - those being garden enthusiasts, prestigious homes and businesses that are after top of the line gardening services like no other on the market.
I am not a typical lawn mowing business so I don't want a typical card design that represents that. The gardens I work with are generally million dollar properties with owners who are very garden proud looking for upkeep and guidance from me along with sometimes whole new garden designs. I want the business cards to show to my clients that I take pride, as they do, in their garden. And I want them to know from my card that I am a professional, qualified horticulturist offering them a top of the line service for life. I want them to refer my business on. I want them to look at my business card and see class and professionalism in a modern unique bold way.
The card should be simple with the possibility of the logo on the front being embossed/debossed and my details on the back the card should have a organic garden feel it's very important to me that it is absolutely perfect
I am also very open to ideas and suggestions so look forward to seeing the designs. the business logo has been supplied with this project and I want the card to be double sided

Contact info is
Colin Barrow - Managing Director / Horticulturist
Phone : 0481 526 704
Email: colinbarrow@verdantterraces.example.au

Target Market(s)

high class gardens residential and commercial

Industry/Entity Type

Gardener

Contact Information for Business Card

Contact info is
Phone : 0481 526 704

PLEASE MAKE CARD DOUBLE SIDED

Requirements
Must have
• organic simple classy modern feel
• must flow with the current logo that has been supplied with this project
• Double sided
• Must explain in a simple way that I deal with high end gardens and I'm a qualified horticulturist
Nice to have
• embossed debossed logo
Should not have
• shouldn't be to busy or cheap looking

```html
<!DOCTYPE html>
<html lang="en">
<head>
<meta charset="utf-8">
<title>Verdant Terraces – Business Card</title>
<link rel="stylesheet" href="https://fonts.googleapis.com/css2?family=Montserrat:wght@300;400;700&display=swap">
<style>
  :root {
    --leaf: #5ea55e;
    --leaf-deep: #4f9350;
    --paper: #ffffff;
    --backdrop: #2b2b2d;
  }
  * { box-sizing: border-box; margin: 0; padding: 0; }
  html, body {
    width: 1200px; height: 900px; overflow: hidden;
    background: var(--backdrop);
    font-family: "Montserrat", sans-serif;
  }
  .sheet {
    width: 1200px; height: 900px;
    display: flex; flex-direction: column;
    align-items: center; justify-content: center; gap: 56px;
  }
  .card {
    position: relative;
    width: 660px; height: 377px;
    border-radius: 22px;
    overflow: hidden;
  }
  /* front side */
  .card-front { background: var(--leaf); }
  .card-front .edge-band {
    position: absolute; left: 0; right: 0; bottom: 0; height: 20px;
    background: var(--paper);
  }
  .card-front .edge-tick {
    position: absolute; left: 56%; bottom: 20px;
    width: 4px; height: 14px; background: var(--paper);
  }
  .brand-mark {
    position: absolute; inset: 0 0 20px 0;
    display: flex; align-items: center; justify-content: center; gap: 18px;
  }
  .brand-dot {
    width: 44px; height: 44px; border-radius: 50%;
    background: var(--leaf-deep);
  }
  .brand-name {
    font-weight: 400; font-size: 38px;
    letter-spacing: 0.14em; text-transform: uppercase;
    color: var(--leaf-deep);
  }
  /* back side */
  .card-back { background: var(--paper); }
  .card-back .edge-band {
    position: absolute; left: 0; right: 0; bottom: 0; height: 20px;
    background: var(--leaf);
  }
  .card-back .edge-tick {
    position: absolute; left: 68%; bottom: 20px;
    width: 4px; height: 14px; background: var(--leaf);
  }
  .details {
    position: absolute; inset: 0 0 20px 0;
    display: flex; flex-direction: column; align-items: center; justify-content: center;
    color: var(--leaf); text-align: center;
  }
  .details .brand-mark-small {
    display: flex; align-items: center; gap: 10px; margin-bottom: 22px;
  }
  .details .brand-mark-small .brand-dot { width: 70px; height: 70px; background: var(--leaf); }
  .details .brand-mark-small .brand-name { font-size: 15px; color: var(--leaf); }
  .person-name { font-weight: 700; font-size: 30px; line-height: 1.1; }
  .person-role { font-weight: 300; font-size: 17px; margin-top: 4px; }
  .contact-icons { display: flex; gap: 8px; margin-top: 14px; }
  .contact-icons svg { width: 13px; height: 13px; }
  .contact-line { font-weight: 300; font-size: 17px; margin-top: 6px; }
</style>
</head>
<body>
<main class="sheet">
  <section class="card card-front" aria-label="Card front">
    <div class="brand-mark">
      <span class="brand-dot"></span>
      <span class="brand-name">verdant terraces</span>
    </div>
    <div class="edge-tick"></div>
    <div class="edge-band"></div>
  </section>

  <section class="card card-back" aria-label="Card back">
    <div class="details">
      <div class="brand-mark-small">
        <span class="brand-dot"></span>
        <span class="brand-name">verdant terraces</span>
      </div>
      <p class="person-name">Colin Barrow</p>
      <p class="person-role">Managing Director / Horticulturist</p>
      <div class="contact-icons">
        <svg viewBox="0 0 24 24" aria-label="Phone"><path fill="#5ea55e" d="M6.6 10.8a15 15 0 0 0 6.6 6.6l2.2-2.2a1 1 0 0 1 1-.25 11.4 11.4 0 0 0 3.6.57 1 1 0 0 1 1 1V20a1 1 0 0 1-1 1A17 17 0 0 1 3 4a1 1 0 0 1 1-1h3.5a1 1 0 0 1 1 1c0 1.25.2 2.45.57 3.57a1 1 0 0 1-.25 1z"/></svg>
        <svg viewBox="0 0 24 24" aria-label="Email"><rect x="3" y="5" width="18" height="14" rx="1.5" fill="none" stroke="#5ea55e" stroke-width="2"/><path d="M3.5 6l8.5 7 8.5-7" fill="none" stroke="#5ea55e" stroke-width="2"/></svg>
      </div>
      <p class="contact-line">0481 526 704</p>
      <p class="contact-line">colinbarrow@verdantterraces.example.au</p>
    </div>
    <div class="edge-tick"></div>
    <div class="edge-band"></div>
  </section>
</main>
</body>
</html>
```